Business card for Luxury Portable Restroom Trailer company

We are a Luxury Portable Restroom Trailer Company Called FALCRIDGE HIRES. Based in Orange County California. We provide portable restroom trailers for events, such as, Weddings, Concerts, Charity events, Sporting events, Tournaments, Corporate events, ect. We rent and Sell the Luxury restrooms. Our colors are white, grey, and Orange. As you will see in the logo we uploaded.
There are 2 people in the company so the names and titles will change for the 3 people but card will remain the same. Here is the information for each Person: Dwight Penner CFO 555 318-0476
next Person: Leon Marchetti VP 555 318-0476
Next Person: Owen Marchetti CEO 555 318-0476
Information to include on the card: Luxury Restroom Trailers Rental and Sales. Weddings, Concerts, Charity, Sporting and Corp. Events.

```html
<!DOCTYPE html>
<html lang="en">
<head>
<meta charset="UTF-8">
<title>Falcridge Hires – Business Card</title>
<link rel="stylesheet" href="https://fonts.googleapis.com/css2?family=Montserrat:wght@400;500;700;800&display=swap">
<style>
  :root {
    --page: #2a2a2d;
    --card: #1c1c1e;
    --card-back: #141415;
    --orange: #f26a21;
    --text: #e6e6e6;
    --muted: #6b6b70;
    --faint: #232325;
    --faint-line: #2c2c2f;
  }
  * { margin: 0; padding: 0; box-sizing: border-box; }
  html, body {
    width: 1200px; height: 900px; overflow: hidden;
    background: var(--page);
    font-family: "Montserrat", sans-serif;
  }
  .canvas {
    position: relative; width: 1200px; height: 900px;
    display: flex; flex-direction: column; align-items: center; justify-content: center; gap: 44px;
  }
  .card {
    position: relative; width: 620px; height: 354px;
    border-radius: 22px; overflow: hidden;
    box-shadow: 0 18px 40px rgba(0,0,0,.45);
  }
  /* Back side */
  .card-back {
    background: var(--card-back);
    display: flex; flex-direction: column; align-items: center; justify-content: center; gap: 22px;
  }
  .back-wordmark {
    font-weight: 800; font-size: 54px; letter-spacing: 2px;
    color: #0c0c0d;
  }
  .services {
    text-align: center;
    font-weight: 500; font-size: 13px; line-height: 1.6; letter-spacing: .3px;
    color: var(--muted);
  }
  .services strong { font-weight: 700; color: var(--orange); }
  /* Front side */
  .card-front { background: var(--card); }
  .front-decoration {
    position: absolute; right: -70px; top: -70px;
    width: 330px; height: 330px; border-radius: 50%;
    background: var(--faint);
    border: 2px solid var(--faint-line);
  }
  .front-content { position: absolute; left: 44px; top: 52px; }
  .brand-name {
    font-weight: 800; font-size: 26px; letter-spacing: 1px;
    color: var(--orange); margin-bottom: 46px;
  }
  .person-name {
    font-weight: 700; font-size: 24px; color: var(--orange); line-height: 1.1;
  }
  .person-title {
    font-weight: 400; font-size: 14px; color: var(--text); margin-bottom: 18px;
  }
  .address {
    font-size: 13px; color: var(--text); line-height: 1.4; margin-bottom: 16px;
  }
  .contact-list { list-style: none; }
  .contact-list li {
    display: flex; align-items: center; gap: 10px;
    font-size: 13px; color: var(--text); line-height: 1.65;
  }
  .contact-list svg { width: 12px; height: 12px; fill: var(--orange); flex: none; }
</style>
</head>
<body>
<main class="canvas">
  <section class="card card-back">
    <div class="back-wordmark">FALCRIDGE HIRES</div>
    <p class="services">
      <strong>Luxury Restroom Trailers Rental and Sales.</strong><br>
      Weddings, Concerts, Charity, Sporting and Corp. Events.
    </p>
  </section>

  <section class="card card-front">
    <div class="front-decoration" role="img" aria-label="Large faint brand emblem area"></div>
    <div class="front-content">
      <div class="brand-name">FALCRIDGE HIRES</div>
      <div class="person-name">Owen Marchetti</div>
      <div class="person-title">CEO</div>
      <div class="address">418 Harbor View Dr, #12<br>Irvine, CA 92614</div>
      <ul class="contact-list">
        <li>
          <svg viewBox="0 0 12 12"><path d="M1 2.5C1 1.7 1.7 1 2.5 1h7C10.3 1 11 1.7 11 2.5V4H8.5V3h-5v1H1z M2 5h8l1 6H1z"/></svg>
          555 318-0476
        </li>
        <li>
          <svg viewBox="0 0 12 12"><path d="M3.5 0h5A1 1 0 0 1 9.5 1v10a1 1 0 0 1-1 1h-5a1 1 0 0 1-1-1V1a1 1 0 0 1 1-1zm.5 1.5v7.5h4V1.5z"/></svg>
          555 318-0476
        </li>
        <li>
          <svg viewBox="0 0 12 12"><path d="M0 2h12v1.2L6 7 0 3.2z M0 4.6l6 3.8 6-3.8V10H0z"/></svg>
          info@falcridgehires.com
        </li>
        <li>
          <svg viewBox="0 0 12 12"><circle cx="6" cy="6" r="5.5"/></svg>
          www.falcridgehires.com
        </li>
      </ul>
    </div>
  </section>
</main>
</body>
</html>
```